Bloom Path! A website showcasing who I am as a person

Bloom Path started out as idea for me to better myself as a person and work on small projects that would help me grow as a person. Now I want to build a website showcasing "Bloom Path." I want the website to showcase who I am and how I have grown both professionally and personally. I can build the raw code of the website on my own but I am not really much of a designer. I am looking for a design where I can write and post blogs, articles and share my thoughts. A little about myself and the ideas and interests that I want to share
What is Bloom Path
Who I am
Background - Professional
Brand Marketing
Email Automation
Hiking
Rock Climbing
Traveling
Exercising and Transformation
"Personal Thoughts"
Hopefully this is enough information to get people started on some designs.
Work
3 page

```html
<!DOCTYPE html>
<html lang="en">
<head>
<meta charset="utf-8">
<title>Dev Malhotra — Bloom Path</title>
<link href="https://fonts.googleapis.com/css2?family=Open+Sans:ital,wght@0,400;0,600;0,700;0,800;1,400&family=Noto+Serif:ital@1&display=swap" rel="stylesheet">
<style>
:root{
  --blue:#2f6fb5;
  --dark:#2b2b2b;
  --footer:#2a2a2a;
  --ink:#222;
  --muted:#777;
  --line:#e2e2e2;
  --page:#f4f4f4;
  --white:#fff;
}
*{box-sizing:border-box;margin:0;padding:0}
html,body{width:1200px;height:2894px;overflow:hidden}
body{position:relative;background:var(--page);font-family:"Open Sans",sans-serif;color:var(--ink)}
.abs{position:absolute}
svg{display:block}

/* top bar */
.topbar{left:0;top:0;width:1200px;height:38px;background:var(--dark);color:#ddd;font-size:10.5px}
.topbar .contact{left:130px;top:12px;display:flex;gap:22px}
.topbar .contact span{display:flex;align-items:center;gap:6px}
.topbar .follow{right:125px;top:11px;display:flex;align-items:center;gap:16px}
.dot{width:10px;height:10px;border-radius:50%;background:#8a8a8a}

/* header */
.header{left:0;top:38px;width:1200px;height:74px;background:var(--white);border-bottom:1px solid var(--line)}
.brand{left:130px;top:20px;font-size:29px;font-weight:600;color:var(--blue);letter-spacing:.3px}
.search{left:874px;top:24px;width:202px;height:28px;background:#eee;border:1px solid #e0e0e0;font-size:9px;color:#aaa;padding:8px 12px;letter-spacing:.5px}
.search svg{position:absolute;right:8px;top:7px}

/* nav */
.nav{left:0;top:112px;width:1200px;height:54px;background:var(--white)}
.nav ul{position:absolute;left:130px;top:0;display:flex;list-style:none;height:54px}
.nav li{font-size:10.5px;font-weight:700;padding:0 15px;line-height:54px;color:#222;text-transform:uppercase}
.nav li.active{color:var(--blue);border-top:3px solid var(--blue);line-height:50px}
.nav .more{left:1000px;top:0;width:76px;height:54px;background:#e7e7e7;font-size:11px;font-weight:700;line-height:54px;text-align:center}

/* hero */
.hero{left:0;top:166px;width:1200px;height:499px;background:linear-gradient(135deg,#6c6259,#4a443f 40%,#3b3a39 70%,#5d544c)}
.hero-title{left:0;top:120px;width:1200px;text-align:center;color:#fff;font-size:52px;font-weight:800;letter-spacing:1px}
.hero-text{left:240px;top:194px;width:720px;text-align:center;color:#fff;font-size:15px;font-weight:600;line-height:30px}
.hero-btn{left:529px;top:279px;width:142px;height:40px;background:var(--blue);border:1px solid #9cc0ea;color:#fff;font-size:12px;font-weight:600;text-align:center;line-height:38px}
.hero-dots{left:558px;top:433px;display:flex;gap:15px}
.hero-dots i{width:17px;height:17px;border-radius:50%;border:2px solid #fff}
.hero-dots i:first-child{background:var(--blue)}
.hero-dots i:last-child{border-color:#d9b25a}

/* section headings */
.sec-title{font-size:21px;font-weight:700;color:var(--ink);display:flex;align-items:center;gap:12px}
.sec-title::after{content:"";height:1px;background:#ccc;flex:1}
.side-title{font-size:15px;font-weight:700;display:flex;align-items:center;gap:12px}
.side-title::after{content:"";width:46px;height:2px;background:var(--blue)}
.arrows{display:flex;gap:4px}
.arrows i{width:12px;height:12px;border-radius:50%;border:1px solid #aaa}
.arrows i:last-child{border-color:#444}

/* cards */
.card{background:var(--white);border:1px solid #e6e6e6;text-align:center;display:flex;flex-direction:column;align-items:center;padding-bottom:28px}
.photo{align-self:stretch;flex:none}
.card h3{font-size:13.5px;font-weight:700;margin-top:22px;color:var(--ink);white-space:nowrap}
.tag{display:inline-flex;align-items:center;gap:10px;font-size:10.5px;color:var(--blue);margin-top:8px;text-transform:uppercase}
.tag::before,.tag::after{content:"";width:28px;height:1px;background:#9bb8dd}
.card p{font-size:11px;color:var(--muted);line-height:22px;margin-top:14px;white-space:nowrap;letter-spacing:-.1px}
.meta{display:flex;justify-content:center;gap:14px;align-items:center;margin-top:12px;font-family:"Noto Serif",serif;font-style:italic;font-size:11px;color:var(--blue);white-space:nowrap}
.meta span{display:flex;align-items:center;gap:5px}
.btn-outline{display:block;border:1px solid var(--blue);color:var(--blue);font-size:10.5px;font-weight:600;padding:10px 0;width:120px;margin-top:auto;text-align:center}

/* sidebar */
.panel{background:var(--white);border:1px solid #e6e6e6}
.about h4{font-size:12px;color:var(--blue);font-weight:700;margin:18px 14px 0}
.about p{font-size:11.5px;color:var(--muted);line-height:20px;margin:10px 14px 0}
.about a{display:block;font-size:10.5px;color:var(--blue);margin:14px 14px 0}
.socials{display:flex;gap:10px;margin:16px 14px 0}
.socials i{width:26px;height:26px;border-radius:50%;border:1px solid #ddd;display:flex;align-items:center;justify-content:center}
.socials i::after{content:"";width:7px;height:7px;border-radius:50%;background:#888}
.archive li{list-style:none;font-size:11.5px;color:#555;display:flex;justify-content:space-between;align-items:center;padding:0 14px;height:31px}
.archive li i{width:15px;height:15px;border-radius:50%;border:1px solid #999}
.pop{display:flex;gap:12px;padding:0 10px;height:88px;align-items:center}
.pop .thumb{width:76px;height:70px;flex:none}
.pop div:last-child{min-width:0}
.pop b{font-size:10.5px;font-weight:400;color:#333;display:block;white-space:nowrap;overflow:hidden;text-overflow:ellipsis}
.pop small{font-size:9.5px;color:#999;display:block;margin-top:10px;white-space:nowrap}
.tweet{display:flex;gap:10px;padding:0 14px}
.tweet .bird{width:14px;height:14px;border-radius:50%;background:#3fa3e0;flex:none;margin-top:2px}
.tweet p{font-size:11px;font-style:italic;color:#777;line-height:19px}
.tweet p em{color:var(--blue)}
.tweet p b{color:#444;font-weight:600}
.tweet small{display:block;font-size:10px;color:var(--blue);margin-top:6px;font-style:normal}
.newsletter .field{margin:14px 14px 0;height:40px;border:1px solid #ddd;font-size:9px;color:#aaa;text-align:center;line-height:38px}
.newsletter .sub{margin:8px 14px 0;height:38px;background:var(--blue);color:#fff;font-size:11px;font-weight:700;text-align:center;line-height:38px}

/* articles */
.article-text{background:var(--white);padding:22px 18px;box-shadow:0 1px 3px rgba(0,0,0,.08)}
.article-text h3{font-size:14px;font-weight:700;white-space:nowrap}
.article-text p{font-size:12px;color:var(--muted);line-height:21px;margin-top:10px}
.article-text .meta{justify-content:flex-start}

/* footer */
.footer{left:0;top:2635px;width:1200px;height:259px;background:var(--footer);color:#bbb}
.footer h5{font-size:13px;font-weight:700;color:#fff;margin-bottom:18px}
.footer .row{display:flex;gap:10px;align-items:center;font-size:11px;margin-bottom:12px}
.footer ul{list-style:none}
.footer li{font-size:10.5px;margin-bottom:13px;display:flex;align-items:center;gap:8px;text-transform:uppercase}
.footer li::before{content:"";border-left:4px solid #aaa;border-top:3px solid transparent;border-bottom:3px solid transparent}
.footer .ring{width:30px;height:30px;border-radius:50%;border:1px solid #777;display:flex;align-items:center;justify-content:center}
.footer .ring::after{content:"";width:8px;height:8px;border-radius:50%;background:#888}
.copy{left:0;top:2838px;width:1200px;border-top:1px solid #3d3d3d;height:56px;font-size:11px;color:#888;text-align:center;line-height:56px}
</style>
</head>
<body>

<div class="abs topbar">
  <div class="abs contact">
    <span><svg width="8" height="11" viewBox="0 0 8 11"><rect x=".5" y=".5" width="7" height="10" rx="1" fill="none" stroke="#ddd"/></svg>CALL US : (2480) 317 902</span>
    <span><svg width="11" height="8" viewBox="0 0 11 8"><rect width="11" height="8" fill="#ddd"/><path d="M0 0l5.5 4L11 0" stroke="#2b2b2b" fill="none"/></svg>EMAIL US : info@devmalhotra.com</span>
  </div>
  <div class="abs follow">FOLLOW US : <i class="dot"></i><i class="dot"></i><i class="dot"></i><i class="dot"></i><i class="dot"></i></div>
</div>

<header class="abs header">
  <div class="abs brand">DEV MALHOTRA</div>
  <div class="abs search">SEARCH<svg width="11" height="11" viewBox="0 0 11 11"><circle cx="4.5" cy="4.5" r="3.5" fill="none" stroke="#888" stroke-width="1.5"/><path d="M7 7l3 3" stroke="#888" stroke-width="1.5"/></svg></div>
</header>

<nav class="abs nav">
  <ul>
    <li class="active">What is Bloom Path</li><li>Who I am</li><li>Background - Professional</li><li>Brand Marketing</li><li>Email Automation</li><li>Hiking</li><li>Rock Climbing</li>
  </ul>
  <div class="abs more">MORE »</div>
</nav>

<section class="abs hero" role="img" aria-label="Overhead photo of a team working together around a wooden table with laptops and coffee">
  <h1 class="abs hero-title">BLOOM PATH</h1>
  <p class="abs hero-text">Lorem ipsum dolor sit amet, consectetur adipiscing elit, sed do eiusmod tempor incididunt labore et dolore magna aliqua. Ut enim ad minim veniam, quis nostrud...</p>
  <div class="abs hero-btn">LEARN MORE INFO</div>
  <div class="abs hero-dots"><i></i><i></i><i></i></div>
</section>

<!-- latest blog -->
<div class="abs" style="left:130px;top:700px;width:635px;display:flex;align-items:center;gap:10px">
  <h2 class="sec-title" style="flex:1">LATEST BLOG</h2><div class="arrows"><i></i><i></i></div>
</div>

<article class="abs card" style="left:130px;top:742px;width:635px;height:553px">
  <div class="photo" role="img" aria-label="Photo of hands working with a laptop, charts and papers on a desk" style="margin:14px 12px 0;height:298px;background:linear-gradient(120deg,#b07a78,#d7c9c5 45%,#8aa3b8)"></div>
  <h3>LABORIS NISI UT ALIQUIP COMMODO CONSEQUAT</h3>
  <div class="tag">Brand Marketing</div>
  <p>Lorem ipsum dolor sit amet, consectetur adipiscing elit, sed do eiusmod tempor incididunt ut labore et<br>dolore magna aliqua. Ut enim ad minim veniam, quis nostrud exercitation ullamco laboris nisi ut aliquip<br>commodo consequat. Duis aute irure dolor in reprehenderit in voluptate...</p>
  <div class="meta"><span><svg width="10" height="10"><rect x=".5" y="1.5" width="9" height="8" fill="none" stroke="#2f6fb5"/><path d="M0 4h10" stroke="#2f6fb5"/></svg>Posted on 23/April/2017</span><span>Share</span><span>Comments</span></div>
  <div class="btn-outline" style="margin-top:14px">LEARN MORE INFO</div>
</article>

<article class="abs card" style="left:130px;top:1318px;width:307px;height:449px">
  <div class="photo" role="img" aria-label="Photo of friends cheering beside a vintage van in a field" style="margin:6px 6px 0;height:200px;background:linear-gradient(180deg,#7fb6dc,#5a9fb0 50%,#8f9a3f)"></div>
  <h3>COMMODO CONSEQUAT</h3><div class="tag">Traveling</div>
  <p>Lorem ipsum dolor sit amet, consectetur adipisci<br>labore et dolore magna aliqua. Ut enim ad minim<br>veniam nostrud exercitation...</p>
  <div class="meta"><span>Posted on 23/April/2017</span><span>‹</span><span>•</span></div>
  <div class="btn-outline">LEARN MORE INFO</div>
</article>
<article class="abs card" style="left:463px;top:1318px;width:302px;height:449px">
  <div class="photo" role="img" aria-label="Photo of hikers crossing a rocky mountain valley" style="margin:6px 6px 0;height:200px;background:linear-gradient(180deg,#9fb0ad,#5d6b5a 55%,#3e4538)"></div>
  <h3>COMMODO CONSEQUAT</h3><div class="tag">Hiking</div>
  <p>Lorem ipsum dolor sit amet, consectetur adipisci<br>labore et dolore magna aliqua. Ut enim ad minim<br>veniam nostrud exercitation...</p>
  <div class="meta"><span>Posted on 23/April/2017</span><span>‹</span><span>•</span></div>
  <div class="btn-outline">LEARN MORE INFO</div>
</article>
<article class="abs card" style="left:130px;top:1790px;width:307px;height:448px">
  <div class="photo" role="img" aria-label="Photo of a climber on a rock face at sunset" style="margin:6px 6px 0;height:200px;background:linear-gradient(180deg,#e8a04c,#b8744a 50%,#4a4038)"></div>
  <h3>COMMODO CONSEQUAT</h3><div class="tag">Rock Climbing</div>
  <p>Lorem ipsum dolor sit amet, consectetur adipisci<br>labore et dolore magna aliqua. Ut enim ad minim<br>veniam nostrud exercitation...</p>
  <div class="meta"><span>Posted on 23/April/2017</span><span>‹</span><span>•</span></div>
  <div class="btn-outline">LEARN MORE INFO</div>
</article>
<article class="abs card" style="left:463px;top:1790px;width:302px;height:448px">
  <div class="photo" role="img" aria-label="Photo of a man working on a laptop at a bright desk" style="margin:6px 6px 0;height:200px;background:linear-gradient(160deg,#e4e2da,#b5a89a 50%,#5c5048)"></div>
  <h3>COMMODO CONSEQUAT</h3><div class="tag">Email Automation</div>
  <p>Lorem ipsum dolor sit amet, consectetur adipisci<br>labore et dolore magna aliqua. Ut enim ad minim<br>veniam nostrud exercitation...</p>
  <div class="meta"><span>Posted on 23/April/2017</span><span>‹</span><span>•</span></div>
  <div class="btn-outline">LEARN MORE INFO</div>
</article>

<!-- sidebar -->
<h2 class="abs side-title" style="left:795px;top:704px">ABOUT ME</h2>
<aside class="abs panel about" style="left:795px;top:748px;width:281px;height:424px">
  <div role="img" aria-label="Portrait photo of the author" style="margin:8px 8px 0;height:170px;background:linear-gradient(180deg,#a9c4da,#8fb0ca)"></div>
  <h4>DEV MALHOTRA</h4>
  <p>Duis aute irure dolor in reprehenderit velit esse cillum dolore eu fugiat nulla Excepteur sint occaecat cupidatat non...</p>
  <p>Esse cillum dolore eu fugiat nulla Excepteur sint occaecat cupidatat non...</p>
  <a>READ MORE INFO &gt;&gt;</a>
  <div class="socials"><i></i><i></i><i></i><i></i><i></i></div>
</aside>

<h2 class="abs side-title" style="left:795px;top:1192px">ARCHIVES</h2>
<ul class="abs panel archive" style="left:795px;top:1230px;width:281px;height:126px">
  <li>September 2016 (18)<i></i></li><li>January 2017 (2)<i></i></li><li>March 2017 (1)<i></i></li><li>April 2017 (1)<i></i></li>
</ul>

<h2 class="abs side-title" style="left:795px;top:1400px">POPULAR POST</h2>
<div class="abs panel" style="left:795px;top:1437px;width:281px;height:353px">
  <div class="pop"><div class="thumb" role="img" aria-label="Photo of a workspace" style="background:linear-gradient(135deg,#c9a893,#6f5b4e)"></div><div><b>It is a long established fact...</b><small>FEB 05, 2017 &nbsp; 4 Comments</small></div></div>
  <div class="pop"><div class="thumb" role="img" aria-label="Photo of a hiker on a summit" style="background:linear-gradient(180deg,#7aa5d6,#a26860)"></div><div><b>It is a long established fact...</b><small>FEB 05, 2017 &nbsp; 4 Comments</small></div></div>
  <div class="pop"><div class="thumb" role="img" aria-label="Photo of a climber on a cliff" style="background:linear-gradient(135deg,#7fa7c9,#a45a52)"></div><div><b>It is a long established fact...</b><small>FEB 05, 2017 &nbsp; 4 Comments</small></div></div>
  <div class="pop"><div class="thumb" role="img" aria-label="Photo of a traveler by the sea" style="background:linear-gradient(180deg,#a8cbe6,#c39a70)"></div><div><b>It is a long established fact...</b><small>FEB 05, 2017 &nbsp; 4 Comments</small></div></div>
</div>

<h2 class="abs side-title" style="left:795px;top:1816px">LATEST TWEETS</h2>
<div class="abs panel" style="left:795px;top:1855px;width:281px;height:215px;padding-top:16px">
  <div class="tweet"><i class="bird"></i><p><em>@Dev Malhotra</em> it is a long established fact that a reader will be <b>distracted by the</b> when looking at its layout.<small>2 month ago</small></p></div>
  <div class="tweet" style="margin-top:18px"><i class="bird"></i><p><em>@Dev Malhotra</em> it is a long established fact that a reader will be <b>distracted by the</b> when looking at its layout.<small>2 month ago</small></p></div>
</div>

<h2 class="abs side-title" style="left:795px;top:2088px">NEWSLETTER</h2>
<div class="abs panel newsletter" style="left:795px;top:2125px;width:281px;height:115px">
  <div class="field">- EMAIL -</div>
  <div class="sub">SUBSCRIBE</div>
</div>

<!-- articles -->
<div class="abs" style="left:130px;top:2276px;width:945px;display:flex;align-items:center;gap:10px">
  <h2 class="sec-title" style="width:600px">ARTICLES</h2><div style="flex:1"></div><div class="arrows"><i></i><i></i></div>
</div>

<div class="abs" role="img" aria-label="Photo of a person working on a laptop with notes" style="left:135px;top:2343px;width:256px;height:222px;background:linear-gradient(135deg,#e9c98f,#a8a8a0 50%,#5d6370)"></div>
<div class="abs article-text" style="left:333px;top:2370px;width:254px;height:170px">
  <h3>DESERUNT MOLLIT ANIM...</h3>
  <p>Lorem ipsum dolor sit amet, consectetur adipiscing elit, sed do eiusmod tempor incididunt occaecat...</p>
  <div class="meta"><span>Posted on 23/April/2017</span><span>‹</span><span>•</span></div>
</div>

<div class="abs" role="img" aria-label="Photo of a hiker with a backpack in snowy mountains" style="left:624px;top:2343px;width:256px;height:222px;background:linear-gradient(180deg,#9db8cf,#d9d4c9 45%,#7a6f5c)"></div>
<div class="abs article-text" style="left:821px;top:2370px;width:254px;height:170px">
  <h3>DESERUNT MOLLIT ANIM...</h3>
  <p>Lorem ipsum dolor sit amet, consectetur adipiscing elit, sed do eiusmod tempor incididunt occaecat...</p>
  <div class="meta"><span>Posted on 23/April/2017</span><span>‹</span><span>•</span></div>
</div>

<!-- footer -->
<footer class="abs footer">
  <div class="abs" style="left:130px;top:38px;width:220px">
    <h5>CONTACT US</h5>
    <div class="row"><svg width="11" height="11"><rect x="1" y="1" width="9" height="9" fill="#bbb"/></svg>(0480)-317-9020 (Phone)</div>
    <div class="row"><svg width="11" height="11"><rect x="1" y="3" width="9" height="6" fill="#bbb"/></svg>(0480)-317-9021 (Fax)</div>
    <div class="row"><svg width="11" height="9"><rect width="11" height="9" fill="#bbb"/><path d="M0 0l5.5 4L11 0" stroke="#2a2a2a" fill="none"/></svg><u>info@devmalhotra.com</u></div>
    <div class="row" style="align-items:flex-start"><svg width="11" height="12"><path d="M5.5 12C2 7 1 5.5 1 4.5a4.5 4.5 0 0 1 9 0C10 5.5 9 7 5.5 12z" fill="#bbb"/></svg>42 Placeholder Lane, Sample<br>Town 0000</div>
  </div>
  <div class="abs" style="left:388px;top:38px">
    <h5>QUICK LINKS</h5>
    <ul><li>What is Bloom Path</li><li>Who I am</li><li>Background - Professional</li><li>Brand Marketing</li><li>Email Automation</li></ul>
  </div>
  <div class="abs" style="left:588px;top:73px">
    <ul><li>Hiking</li><li>Rock Climbing</li><li>Traveling</li><li>Exercising and Transformation</li><li>"Personal Thoughts"</li></ul>
  </div>
  <div class="abs" style="left:878px;top:38px;width:200px">
    <h5>FOLLOW US</h5>
    <p style="font-size:11px;line-height:17px">It is a long established fact that a reader will be distracted by content of a page when looking at its...</p>
    <div style="display:flex;gap:10px;margin-top:16px"><i class="ring"></i><i class="ring"></i><i class="ring"></i><i class="ring"></i></div>
  </div>
</footer>
<div class="abs copy">© 2017 Dev Malhotra . All rights reserved.</div>

</body>
</html>
```